Brightfen Business Card Redesign & Logo Update

We need to update our business cards to something more modern and fresh. Brightfen can provide the current color schemes and old design examples, but welcome creativity in helping us with this redesign. PLEASE NOTE that we no longer utilize the "tree" and/or "leaf" imagery in our branding. If able would apprecaite an update on the quality of our "words only" logo in Ai. / PNG formats too.

Target Market(s)

Investors, landowners, corporate partners, contractors

Industry/Entity Type

Environmental Restoration & Conservation

Contact Information for Business Card

Logo, persons name, title, mailing address, phone and email, website url

Font styles to use
Other font styles liked:
• Merriweather

Requirements
Nice to have
• Logo, persons name, title, mailing address, phone and email, website url, but open to ideams
Should not have
• No all back backgrounds

```html
<!DOCTYPE html>
<html lang="en">
<head>
<meta charset="utf-8">
<title>Brightfen Business Card</title>
<link rel="stylesheet" href="https://fonts.googleapis.com/css2?family=Barlow:wght@600&family=Source+Sans+3:wght@400;700&display=swap">
<style>
  :root {
    --backdrop: #e3e3e3;
    --card: #f4f4f4;
    --orange: #e67821;
    --amber: #eb9a20;
    --green: #13773d;
    --green-light: #2a8f45;
    --ink: #111111;
    --text: #1e1e1e;
  }
  * { margin: 0; padding: 0; box-sizing: border-box; }
  html, body { width: 1200px; height: 960px; overflow: hidden; }
  body {
    background: var(--backdrop);
    position: relative;
    font-family: "Source Sans 3", sans-serif;
    color: var(--text);
  }
  .card {
    position: absolute;
    left: 295px;
    width: 610px;
    height: 349px;
    background: var(--card);
    border-radius: 22px;
    overflow: hidden;
  }
  .card--front { top: 108px; }
  .card--back { top: 511px; }
  .card__waves { position: absolute; inset: 0; width: 610px; height: 349px; }

  .wordmark {
    position: absolute;
    text-align: center;
    white-space: nowrap;
  }
  .wordmark__name {
    display: block;
    font-family: "Source Sans 3", sans-serif;
    font-weight: 700;
    color: var(--green);
    line-height: 1;
  }
  .wordmark__tagline {
    display: block;
    font-family: "Barlow", sans-serif;
    font-weight: 600;
    color: var(--ink);
    line-height: 1;
  }
  .card--front .wordmark { left: 0; width: 610px; top: 110px; }
  .card--front .wordmark__name { font-size: 88px; letter-spacing: 1px; }
  .card--front .wordmark__tagline { font-size: 28px; margin-top: 4px; }

  .card--back .wordmark { left: 45px; width: 270px; top: 132px; }
  .card--back .wordmark__name { font-size: 54px; }
  .card--back .wordmark__tagline { font-size: 17.5px; margin-top: 2px; }

  .contact { position: absolute; left: 354px; top: 76px; }
  .contact__name { font-size: 20px; font-weight: 700; color: var(--green); line-height: 1.1; }
  .contact__title { font-size: 15px; line-height: 1.3; margin-top: 2px; }
  .contact__rule { width: 38px; height: 2px; background: var(--orange); margin: 18px 0 16px; }
  .contact__address { font-size: 15px; line-height: 20px; }
  .contact__list { list-style: none; font-size: 15px; line-height: 20.5px; }
  .contact__list li { display: flex; align-items: center; gap: 5px; }
  .contact__icon { width: 13px; height: 13px; flex: none; }
</style>
</head>
<body>

<section class="card card--front">
  <svg class="card__waves" viewBox="0 0 610 349" aria-hidden="true">
    <path d="M0 0 H610 V66 C520 82 420 70 300 40 C200 15 90 20 0 72 Z" fill="var(--amber)"/>
    <path d="M0 0 H610 V60 C520 72 420 60 300 30 C200 10 90 16 0 72 Z" fill="var(--orange)"/>
    <path d="M0 290 C100 270 200 280 300 305 C420 335 520 330 610 277 V349 H0 Z" fill="var(--green-light)"/>
    <path d="M0 300 C100 282 200 292 300 312 C420 336 520 332 610 280 V349 H0 Z" fill="var(--green)"/>
  </svg>
  <div class="wordmark">
    <span class="wordmark__name">Brightfen</span>
    <span class="wordmark__tagline">Environmental Credit Company</span>
  </div>
</section>

<section class="card card--back">
  <svg class="card__waves" viewBox="0 0 610 349" aria-hidden="true">
    <path d="M0 284 C90 270 200 276 310 298 C420 320 520 328 610 276 V349 H0 Z" fill="var(--orange)"/>
    <path d="M0 290 C100 282 200 288 310 306 C420 324 530 332 610 280 V349 H0 Z" fill="var(--green)"/>
  </svg>
  <div class="wordmark">
    <span class="wordmark__name">Brightfen</span>
    <span class="wordmark__tagline">Environmental Credit Company</span>
  </div>
  <div class="contact">
    <p class="contact__name">Daniel Harper</p>
    <p class="contact__title">Owner</p>
    <div class="contact__rule"></div>
    <p class="contact__address">415 Meadow Lane, Suite 210<br>Fairhaven, CA 95012</p>
    <div class="contact__rule"></div>
    <ul class="contact__list">
      <li>
        <svg class="contact__icon" viewBox="0 0 16 16" aria-hidden="true"><path d="M3.5 1.5 L6 4 L4.6 5.6 C5.4 7.6 8.4 10.6 10.4 11.4 L12 10 L14.5 12.5 L12.8 14.3 C8 14 2 8 1.7 3.2 Z" fill="none" stroke="var(--orange)" stroke-width="1.5" stroke-linejoin="round"/></svg>
        <span>555-204-3817</span>
      </li>
      <li>
        <svg class="contact__icon" viewBox="0 0 16 16" aria-hidden="true"><rect x="1.5" y="3" width="13" height="10" rx="1" fill="none" stroke="var(--orange)" stroke-width="1.5"/><path d="M2 4 L8 9 L14 4" fill="none" stroke="var(--orange)" stroke-width="1.5"/></svg>
        <span>daniel@brightfen.com</span>
      </li>
      <li>
        <svg class="contact__icon" viewBox="0 0 16 16" aria-hidden="true"><g fill="none" stroke="var(--orange)" stroke-width="1.3"><circle cx="8" cy="8" r="6.5"/><ellipse cx="8" cy="8" rx="2.8" ry="6.5"/><path d="M1.5 8 H14.5 M2.6 4.5 H13.4 M2.6 11.5 H13.4"/></g></svg>
        <span>www.brightfen.com</span>
      </li>
    </ul>
  </div>
</section>

</body>
</html>
```